Ten-Harvest Brochure

We would like a 3 panel layout format with copy on both sides and on each panel, (we will provide content).

We are Ten-Harvest and we work with business owners to achieve measurable growth and success based on 5 Core Pillars Of Momentum and (S.L.K) 60 Week Progress Roadmap Scheme. We also work with the business leader and individuals within the organization with personal development.

We would like the brochure to have a corporate feel, but warm and inviting. We don't want a hard or aggressive feel.

We would like it to be available for pdf upload and physical print formats.

The winning design will also be invited to design a header for our website as well. The header will be consistent with the brochure, so please keep that in mind during your creative process.

I am enclosing a transparent copy of our company logo along with content for the brochure.

Thank you in advance for your consideration!

Gareth and Moira
Updates

Sorry, but we forgot to include the front cover text.

It will read as follows,

Do you know the 5 Core Pillars Of Momentum  that are crucial to the success of any business today?

Also, please add the following to the back page

Website: www.ten-harvest.example
Resource Centre: www.thresourcehub.example 
Phone: +44 (0) 7612583047
Email: info@ten-harvest.example

Follow us on (please insert Friendbook, Linkpro and Vidstream logo)

I have uploaded a pdf format of brochure text.

Hello designers. I wanted to give some further input to help the process. Although the brochure is to target business, we don't want to over do it with corporate professioanls in all the photos. If there is an opportunity to incorporate photos of small business owners like, a butcher, baker, chef, flower shop etc. This would hopefully help us make an immpression to all small business owners.

Thank you, and good luck!

Gareth and Moira  

Reason: A few designers have come come on board last minute. So I'd like to give everyone the same opportunity to respond. Sincerely, Gareth

Target Market(s)

Small Business Owners searching for new ways to grow their business in the UK and Republic Of Ireland.

Industry/Entity Type

Business

```html
<!DOCTYPE html>
<html lang="en">
<head>
<meta charset="utf-8">
<title>Ten-Harvest Brochure – Outside</title>
<link href="https://fonts.googleapis.com/css2?family=Open+Sans:wght@400;600;700&family=Oswald:wght@600;700&display=swap" rel="stylesheet">
<style>
  :root {
    --bg: #c9ced3;
    --paper: #fbf9fb;
    --plum: #7b2a7f;
    --plum-dark: #5c1f60;
    --magenta: #b24fae;
    --blush: #f1e2ef;
    --blush-soft: #f8f0f7;
    --ink: #4a2a4c;
    --grey: #6b6b70;
    --teal: #3fb8c4;
  }
  * { box-sizing: border-box; margin: 0; padding: 0; }
  html, body { width: 1200px; height: 769px; overflow: hidden; }
  body {
    background: var(--bg);
    font-family: "Open Sans", Arial, sans-serif;
    color: var(--ink);
    display: flex;
    align-items: center;
    justify-content: center;
  }
  .brochure {
    display: flex;
    width: 1050px;
    height: 680px;
    box-shadow: 0 10px 30px rgba(60, 40, 70, .25);
  }
  .panel {
    position: relative;
    width: 350px;
    height: 100%;
    background: var(--paper);
    overflow: hidden;
  }
  .panel + .panel { border-left: 1px solid #e6dde6; }
  .panel-waves { position: absolute; inset: 0; width: 100%; height: 100%; }
  .panel-content { position: relative; padding: 0 34px; }

  .ribbon {
    display: inline-block;
    background: var(--plum);
    color: #fff;
    font-size: 14px;
    font-weight: 400;
    padding: 7px 30px 7px 28px;
    clip-path: polygon(0 0, 100% 0, 92% 50%, 100% 100%, 0 100%, 8% 50%);
  }
  .ribbon-wrap { text-align: center; }

  .body-copy {
    font-size: 12.5px;
    line-height: 1.55;
    color: var(--plum);
    text-align: justify;
  }
  .body-copy strong { font-weight: 700; }

  /* Left panel */
  .panel-left .panel-content { padding-top: 78px; }
  .panel-left .ribbon-wrap { margin-bottom: 18px; }
  .panel-left .body-copy { text-indent: 70px; }
  .section-after { margin-top: 34px; }
  .section-after .ribbon-wrap { text-align: left; margin-left: -34px; margin-bottom: 16px; }
  .section-after .ribbon { clip-path: polygon(0 0, 100% 0, 94% 50%, 100% 100%, 0 100%); padding-left: 34px; }
  .area-list { list-style: none; margin: 14px 0 18px 4px; }
  .area-list li {
    font-size: 12.5px;
    color: var(--plum);
    line-height: 1.45;
    padding-left: 28px;
    position: relative;
  }
  .area-list li::before {
    content: "";
    position: absolute;
    left: 4px; top: 6px;
    width: 6px; height: 6px;
    border-top: 2px solid var(--ink);
    border-right: 2px solid var(--ink);
    transform: rotate(45deg);
  }

  /* Middle panel */
  .photo-handset {
    position: relative;
    height: 175px;
    margin: 0 -34px;
    background: linear-gradient(160deg, #e9e4e8 0%, #b9aeb6 45%, #3b3538 75%, #d9cfd6 100%);
    clip-path: ellipse(80% 100% at 50% 0);
  }
  .panel-middle .ribbon-wrap { margin-top: 22px; }
  .brand {
    display: flex;
    align-items: center;
    justify-content: center;
    gap: 8px;
    margin: 26px 0 30px;
  }
  .brand-mark { width: 14px; height: 14px; background: var(--grey); }
  .brand-name {
    font-size: 17px;
    font-weight: 600;
    letter-spacing: 2px;
    text-transform: uppercase;
    color: var(--grey);
  }
  .contact-list { list-style: none; }
  .contact-list li {
    display: flex;
    align-items: center;
    gap: 18px;
    font-size: 13px;
    color: var(--ink);
    margin-bottom: 14px;
  }
  .contact-icon {
    flex: none;
    width: 24px; height: 20px;
    background: var(--plum);
    display: flex; align-items: center; justify-content: center;
  }
  .resource-note {
    text-align: center;
    font-size: 13px;
    line-height: 1.45;
    color: var(--ink);
    margin: 12px 0 24px;
  }
  .social-list { list-style: none; margin-left: 88px; }
  .social-list li {
    display: flex; align-items: center; gap: 10px;
    font-size: 11.5px; font-weight: 600; color: var(--ink);
    margin-bottom: 5px;
  }
  .social-dot { width: 10px; height: 10px; background: var(--plum-dark); }

  /* Right panel (cover) */
  .panel-cover .brand { justify-content: flex-start; margin: 30px 0 0 70px; }
  .cover-band {
    position: absolute;
    left: 0; right: 0; top: 150px;
    height: 150px;
    background: linear-gradient(135deg, var(--plum) 0%, var(--magenta) 100%);
    clip-path: polygon(0 22%, 100% 0, 100% 78%, 0 100%);
  }
  .cover-question {
    position: absolute;
    left: 40px; right: 30px; top: 182px;
    text-align: center;
    font-family: "Oswald", "Arial Narrow", sans-serif;
    font-weight: 700;
    font-size: 19px;
    line-height: 1.22;
    color: #fff;
    transform: rotate(-6deg);
  }
  .cover-question em { font-style: normal; color: #f0b6ea; }
  .cover-art {
    position: absolute;
    left: 60px; top: 330px;
    width: 230px; height: 200px;
    background: radial-gradient(circle at 60% 45%, #d98ad5 0%, #c065bb 35%, #8ad4dc 70%, rgba(250,246,250,0) 100%);
    border-radius: 6px;
  }
  .cover-base {
    position: absolute;
    left: 0; right: 0; bottom: 0; height: 200px;
    background: linear-gradient(160deg, var(--magenta) 0%, var(--plum-dark) 100%);
    clip-path: polygon(0 55%, 100% 0, 100% 100%, 0 100%);
  }
</style>
</head>
<body>
  <main class="brochure">

    <section class="panel panel-left">
      <svg class="panel-waves" viewBox="0 0 350 680" preserveAspectRatio="none" aria-hidden="true">
        <path d="M0 30 C120 0 230 40 350 10 L350 0 L0 0Z" fill="var(--blush)"/>
        <path d="M0 280 C120 240 240 300 350 250 L350 300 C240 340 120 290 0 320Z" fill="var(--blush-soft)"/>
        <path d="M0 660 C120 620 240 690 350 640 L350 680 L0 680Z" fill="var(--blush)"/>
      </svg>
      <div class="panel-content">
        <div class="ribbon-wrap"><span class="ribbon">Getting Started!</span></div>
        <p class="body-copy">The first step is to visit <strong>www.ten-harvest.example</strong> or call <strong>+44 (0) 7612583047</strong> to book your <strong>FREE CONSULTATION</strong>. This will be an opportunity for you to think about where you want your business to go and for us to establish how we can get you there.</p>

        <div class="section-after">
          <div class="ribbon-wrap"><span class="ribbon">After That?</span></div>
          <p class="body-copy">We will carry out a business analysis based on <strong>The 5 Core Pillars Of Momentum.</strong></p>
          <ul class="area-list">
            <li>Your Brand</li>
            <li>Sales</li>
            <li>Your People</li>
            <li>Product &amp; Service</li>
            <li>Psychology &amp; Skills</li>
            <li>Finance</li>
          </ul>
          <p class="body-copy">We then provide you with a detailed report and work with you to create and implement your Progress Roadmap Scheme (S.L.K.). This is a 60 week plan, customized for your business and designed so you can start seeing positive and measurable results immediately.</p>
        </div>
      </div>
    </section>

    <section class="panel panel-middle">
      <svg class="panel-waves" viewBox="0 0 350 680" preserveAspectRatio="none" aria-hidden="true">
        <path d="M0 250 C120 200 240 280 350 220 L350 290 C240 340 120 270 0 320Z" fill="var(--blush-soft)"/>
        <path d="M0 640 C120 610 240 670 350 630 L350 680 L0 680Z" fill="var(--blush)"/>
      </svg>
      <div class="panel-content">
        <div class="photo-handset" role="img" aria-label="Photo of a hand lifting a black office telephone handset"></div>
        <div class="ribbon-wrap"><span class="ribbon">Get in Touch!</span></div>
        <div class="brand">
          <span class="brand-mark"></span>
          <span class="brand-name">Ten-Harvest</span>
        </div>
        <ul class="contact-list">
          <li><span class="contact-icon"><svg width="14" height="10" viewBox="0 0 14 10"><path d="M1 1 L4 9 L7 3 L10 9 L13 1" stroke="#fff" stroke-width="1.6" fill="none"/></svg></span>www.ten-harvest.example</li>
          <li><span class="contact-icon"><svg width="12" height="12" viewBox="0 0 12 12"><path d="M2 1 L4.5 1 L5.5 3.8 L4 5 C4.8 6.8 5.8 7.8 7.4 8.4 L8.6 7 L11 8 L11 10.6 C6 11 1 6 2 1Z" fill="#fff"/></svg></span>+44 (0) 7612583047</li>
          <li><span class="contact-icon"><svg width="12" height="12" viewBox="0 0 12 12"><circle cx="6" cy="6" r="2.4" stroke="#fff" stroke-width="1.4" fill="none"/><path d="M8.4 6 C8.4 8 11 8 11 6 A5 5 0 1 0 8.5 10.3" stroke="#fff" stroke-width="1.4" fill="none"/></svg></span>info@ten-harvest.example</li>
        </ul>
        <p class="resource-note">Visit our Resource Center at<br>www.thresourcehub.example</p>
        <ul class="social-list">
          <li><span class="social-dot"></span>Friendbook!</li>
          <li><span class="social-dot"></span>Linkpro!</li>
          <li><span class="social-dot"></span>Vidstream!</li>
        </ul>
      </div>
    </section>

    <section class="panel panel-cover">
      <svg class="panel-waves" viewBox="0 0 350 680" preserveAspectRatio="none" aria-hidden="true">
        <path d="M0 140 C120 120 240 150 350 110 L350 140 C240 180 120 150 0 170Z" fill="var(--blush)"/>
      </svg>
      <div class="panel-content">
        <div class="brand">
          <span class="brand-mark"></span>
          <span class="brand-name">Ten-Harvest</span>
        </div>
      </div>
      <div class="cover-band"></div>
      <h1 class="cover-question">Do you know the <em>5 Core Pillars Of Momentum</em> that are crucial to the success of any business today?</h1>
      <div class="cover-base"></div>
      <div class="cover-art" role="img" aria-label="Illustration of a rising magenta arrow beside the word profit in 3D lettering"></div>
    </section>

  </main>
</body>
</html>
```